Local Flower Farm Needs Business Card Design

I need business cards designed for a flower farm based in Eudora, Kansas.
Business Info:
We are a local cut flower farm located in Eudora, Kansas, founded by Corinne Haldwick. What started as a passion for agriculture and search for more joy in daily life has blossomed into a small business dedicated to providing the community with beautiful, fresh, and sustainable flowers. We specialize in local, seasonal blooms, ensuring that every petal reflects the care and dedication we pour into our craft. Our mission is to deliver the highest quality flowers directly to our customers through local farmers markets and to florists who share our commitment to sustainability. Join us in celebrating the beauty of nature, one bloom at a time!
Contact Details:
Corinne Haldwick
Owner
Phone 913-555-0147
Facebook: Rosalind Thorpe Gardens
Instagram: @RosalindThorpeGardens
Website: RosalindThorpeGardens.example
Target Market(s)
Wholesale to Florists and Direct to Consumer via Farmers Market
Industry/Entity Type
Florist, Farm
Contact Information for Business Card
Name, Contact Info, Logo
Look and feel
Each slider illustrates characteristics of the customer's brand and the style your logo design should communicate.

```html
<!DOCTYPE html>
<html lang="en">
<head>
<meta charset="utf-8">
<title>Rosalind Thorpe Gardens — Business Card</title>
<link href="https://fonts.googleapis.com/css2?family=Tinos:wght@400;700&display=swap" rel="stylesheet">
<style>
  :root {
    --backdrop: #e3e7e9;
    --evergreen: #0b2a30;
    --paper: #ffffff;
    --ink: #111111;
  }
  * { margin: 0; padding: 0; box-sizing: border-box; }
  html, body { width: 1200px; height: 960px; overflow: hidden; }
  body {
    background: var(--backdrop);
    font-family: "Tinos", "Times New Roman", serif;
    position: relative;
  }
  .card {
    position: absolute;
    top: 106px;
    width: 429px;
    height: 750px;
    border-radius: 26px;
    overflow: hidden;
  }
  .card--front { left: 142px; background: var(--evergreen); }
  .card--back { left: 631px; background: var(--paper); color: var(--ink); }

  .brand-seal {
    position: absolute;
    display: flex;
    align-items: center;
    justify-content: center;
    text-align: center;
    border-radius: 50%;
  }
  .card--front .brand-seal {
    left: 64px; top: 224px;
    width: 300px; height: 300px;
    border: 1.5px solid var(--paper);
    color: var(--paper);
    font-size: 34px;
    line-height: 1.15;
    letter-spacing: 1px;
  }
  .card--back .brand-seal {
    left: 111px; top: 25px;
    width: 206px; height: 206px;
    border: 1.5px solid var(--evergreen);
    color: var(--evergreen);
    font-size: 24px;
    line-height: 1.15;
    letter-spacing: 0.5px;
  }

  .holder { position: absolute; left: 59px; top: 512px; }
  .holder-name {
    font-weight: 700;
    font-size: 37px;
    letter-spacing: 0.6px;
    line-height: 1;
  }
  .holder-role { font-size: 18px; margin-top: 6px; letter-spacing: 0.3px; }

  .contact-list {
    position: absolute;
    left: 59px; top: 606px;
    list-style: none;
  }
  .contact-item {
    display: flex;
    align-items: center;
    height: 25.5px;
    font-size: 18.5px;
    letter-spacing: 0.4px;
  }
  .contact-icon { width: 19px; height: 19px; margin-right: 9px; flex: none; }
</style>
</head>
<body>

<section class="card card--front" aria-label="Card front">
  <div class="brand-seal">Rosalind Thorpe<br>Gardens</div>
</section>

<section class="card card--back" aria-label="Card back">
  <div class="brand-seal">Rosalind Thorpe<br>Gardens</div>

  <div class="holder">
    <h1 class="holder-name">Corinne Haldwick</h1>
    <p class="holder-role">Owner</p>
  </div>

  <ul class="contact-list">
    <li class="contact-item">
      <svg class="contact-icon" viewBox="0 0 20 20" aria-hidden="true">
        <path d="M4 2.5l3 .5 1.2 3.6-1.9 1.5c1 2.2 2.6 3.8 4.8 4.8l1.5-1.9 3.6 1.2.5 3c-.2.8-1 1.4-1.8 1.4C8.3 16.6 3.4 11.7 2.6 4.3 2.6 3.5 3.2 2.7 4 2.5z" fill="#0b2a30"/>
      </svg>
      913-555-0147
    </li>
    <li class="contact-item">
      <svg class="contact-icon" viewBox="0 0 20 20" aria-hidden="true">
        <circle cx="10" cy="10" r="9" fill="#0b2a30"/>
      </svg>
      Rosalind Thorpe Gardens
    </li>
    <li class="contact-item">
      <svg class="contact-icon" viewBox="0 0 20 20" aria-hidden="true">
        <rect x="1.5" y="1.5" width="17" height="17" rx="4" fill="none" stroke="#0b2a30" stroke-width="2"/>
      </svg>
      @RosalindThorpeGardens
    </li>
    <li class="contact-item">
      <svg class="contact-icon" viewBox="0 0 20 20" aria-hidden="true">
        <circle cx="10" cy="10" r="8.5" fill="none" stroke="#0b2a30" stroke-width="1.6"/>
        <ellipse cx="10" cy="10" rx="3.6" ry="8.5" fill="none" stroke="#0b2a30" stroke-width="1.4"/>
        <line x1="1.5" y1="10" x2="18.5" y2="10" stroke="#0b2a30" stroke-width="1.4"/>
      </svg>
      RosalindThorpeGardens.example
    </li>
  </ul>
</section>

</body>
</html>
```